Pemberlux: Smart Quotes for Wine Lovers

Hello. I am completing book of quotes for wine lovers. Need the text formatted so that it is easy to read and aesthetically pleasing...modern, clean, smart. Number the pages. The cover is complete. Book is small square. 7.5 by 7.5 inches. If you want to show me first few pages that would be awesome. Thank you!
Updates

I edited the quotes so if you downloaded first ones, please grab these ones instead, thank you! 

Target Market(s)

wine lovers. Urban. Modern.

Industry/Entity Type

Quotes

Requirements
Should not have
• No color. black and white only.

```html
<!DOCTYPE html>
<html lang="en">
<head>
<meta charset="utf-8">
<title>Pemberlux: Smart Quotes for Wine Lovers</title>
<link rel="stylesheet" href="https://fonts.googleapis.com/css2?family=Noto+Sans:wght@400;700&display=swap">
<style>
  :root {
    --paper: #ffffff;
    --ink: #111111;
    --ink-muted: #8a8a8a;
    --gutter: #c8c8c8;
  }
  * { margin: 0; padding: 0; box-sizing: border-box; }
  html, body {
    width: 1200px;
    height: 600px;
    overflow: hidden;
    background: var(--paper);
  }
  body {
    font-family: "Noto Sans", Verdana, sans-serif;
    color: var(--ink);
  }
  .spread {
    position: relative;
    width: 1200px;
    height: 600px;
    background: var(--paper);
  }
  .gutter {
    position: absolute;
    left: 600px;
    top: 0;
    width: 1px;
    height: 600px;
    background: var(--gutter);
  }
  .page {
    position: absolute;
    top: 0;
    width: 600px;
    height: 600px;
  }
  .page--left { left: 0; }
  .page--right { left: 601px; }

  .quote {
    position: absolute;
    top: 207px;
    font-size: 40px;
    line-height: 49px;
    letter-spacing: 0.02em;
    font-weight: 400;
  }
  .page--left .quote {
    right: 140px;
    text-align: right;
  }
  .page--right .quote {
    left: 138px;
    text-align: left;
  }
  .attribution {
    display: block;
    margin-top: 14px;
    font-size: 13.5px;
    line-height: 18px;
    letter-spacing: 0.08em;
  }
  .page--right .attribution { margin-top: 12px; }

  .footnote {
    position: absolute;
    top: 518px;
    font-size: 7.6px;
    line-height: 10px;
    font-weight: 700;
  }
  .page--left .footnote {
    right: 140px;
    width: 280px;
    text-align: right;
  }
  .page--right .footnote {
    left: 138px;
    width: 290px;
    color: var(--ink-muted);
  }

  .folio {
    position: absolute;
    top: 523px;
    font-size: 13.5px;
    line-height: 18px;
  }
  .page--left .folio { left: 77px; }
  .page--right .folio { right: 77px; }
</style>
</head>
<body>
  <main class="spread">
    <section class="page page--left">
      <blockquote class="quote">
        The connoisseur<br>does not drink<br>wine but tastes<br>its secrets
        <cite class="attribution">–ANSEL MORVANE</cite>
      </blockquote>
      <p class="footnote">Anselmo Tomás Morvane i Castellet, 1st Marqués de Vellaró (1904–1989) Spanish Surrealist Painter.</p>
      <span class="folio">34</span>
    </section>

    <div class="gutter"></div>

    <section class="page page--right">
      <blockquote class="quote">
        Wine is the<br>divine juice of<br>September
        <cite class="attribution">–VELLANCE</cite>
      </blockquote>
      <p class="footnote">Jean-Luc Davrenne &nbsp;known by his "nom de plume" Vellance.<br>(1694 –1778). French Enlightenment Writer, Historian and Philosopher.</p>
      <span class="folio">35</span>
    </section>
  </main>
</body>
</html>
```